Business card design for Automotive workshop

We need a business card for a new automotive repair and tyre shop called Keelstone Prime Automotive located in New Zealand. We are a clean, modern and fresh workshop and company.

Front needs to feature logo,
my name:
Marlo Fenwicke (director)

Address:
48 Tarn Lane
Kauriwai 3592

Phone: 07 594 2713
Mobile: 027 451 9362
Email: office@keelstoneautomotive.example.nz
Website: keelstoneautomotive.example.nz

Back needs to feature an area to write down appointment details, date and time.

Also feature a list of jobs and work we do such as,
Vehicle Servicing
All Mechanical Repairs
Warrant of Fitness
Tyres & Wheel Alignments
Automotive Diagnostics
Automotive Parts & Supplies

```html
<!DOCTYPE html>
<html lang="en">
<head>
<meta charset="utf-8">
<title>Keelstone Prime Automotive – Business Card</title>
<link href="https://fonts.googleapis.com/css2?family=Open+Sans:wght@400;600;700;800&display=swap" rel="stylesheet">
<style>
  :root {
    --backdrop: #0c0c0d;
    --card: #2a2a2c;
    --edge-red: #d7101e;
    --brand-red: #e3131f;
    --text-light: #f2f2f2;
    --text-muted: #d0d0d0;
    --emboss: #5a5a5e;
    --field: #9c9c9e;
  }
  * { margin: 0; padding: 0; box-sizing: border-box; }
  html, body {
    width: 1200px; height: 822px; overflow: hidden;
    background: var(--backdrop);
    font-family: "Open Sans", Arial, sans-serif;
  }
  .stage {
    width: 1200px; height: 822px;
    display: flex; align-items: center; justify-content: center; gap: 60px;
  }
  .card {
    width: 520px; height: 300px;
    background: var(--card);
    border-bottom: 3px solid var(--edge-red);
    border-left: 2px solid var(--edge-red);
    box-shadow: 0 18px 40px rgba(0,0,0,.6);
    position: relative;
    color: var(--text-light);
  }
  /* Front */
  .card--front {
    display: flex; flex-direction: column; align-items: center;
    padding-top: 26px; text-align: center;
  }
  .holder-name {
    color: var(--brand-red); font-weight: 700; font-size: 17px; letter-spacing: .5px;
  }
  .holder-role { font-size: 11px; color: var(--text-light); margin-top: -2px; }
  .brand-name {
    margin-top: 10px; color: var(--brand-red); font-weight: 800;
    font-size: 24px; letter-spacing: 1px; text-transform: uppercase; line-height: 1.1;
  }
  .address { margin-top: 12px; font-size: 12.5px; }
  .divider { width: 74px; height: 1px; background: var(--brand-red); margin: 7px 0; }
  .contact-line { font-size: 12px; line-height: 1.55; }
  .contact-line b { color: var(--brand-red); font-weight: 600; }
  .services { font-size: 12.5px; line-height: 1.6; }
  .services .bullet {
    display: inline-block; width: 5px; height: 5px; background: var(--brand-red);
    margin: 0 6px; vertical-align: middle;
  }
  /* Back */
  .card--back {
    border-bottom-width: 6px;
    display: flex; flex-direction: column; align-items: center; justify-content: center;
  }
  .back-brand {
    color: var(--emboss); font-weight: 800; font-size: 26px; letter-spacing: 2px;
    text-transform: uppercase; line-height: 1.15; text-align: center;
  }
  .appointment-title {
    margin-top: 28px; font-weight: 700; font-size: 15px; color: var(--text-muted);
    letter-spacing: .3px;
  }
  .appointment-fields {
    margin-top: 16px; display: flex; gap: 34px; align-items: center;
  }
  .field { display: flex; align-items: center; gap: 10px; font-size: 14px; color: var(--text-light); }
  .field-box {
    width: 110px; height: 28px; border-radius: 14px; background: var(--field);
  }
</style>
</head>
<body>
<main class="stage">
  <section class="card card--front" aria-label="Business card front">
    <div class="holder-name">MARLO FENWICKE</div>
    <div class="holder-role">Director</div>
    <div class="brand-name">Keelstone Prime<br>Automotive</div>
    <div class="address">48 Tarn Lane, Kauriwai 3592</div>
    <div class="divider"></div>
    <div class="contact-line"><b>P:</b> 07 594 2713 | <b>E:</b> 027 451 9362 | <b>W:</b> keelstoneautomotive.example.nz</div>
    <div class="contact-line"><b>E:</b> office@keelstoneautomotive.example.nz</div>
    <div class="divider"></div>
    <div class="services">
      Vehicle Servicing<span class="bullet"></span>All Mechanical Repairs<span class="bullet"></span>Automotive Parts &amp; Supplies<br>
      Tyres &amp; Wheel Alignments<span class="bullet"></span>Automotive Diagnostics<span class="bullet"></span>Warrant of Fitness
    </div>
  </section>

  <section class="card card--back" aria-label="Business card back">
    <div class="back-brand">Keelstone Prime<br>Automotive</div>
    <div class="appointment-title">NEXT APPOINTMENT</div>
    <div class="appointment-fields">
      <div class="field">DATE <span class="field-box"></span></div>
      <div class="field">TIME <span class="field-box"></span></div>
    </div>
  </section>
</main>
</body>
</html>
```